Brightwell Practice Partners, Inc (www.brightwellpracticepartnrs.example) would like to design a website to convey a level of professionalism to healthcare providers that we are the place form them to visit for Contin. Education, Marketing and Management, Joint Venture Partnerships, etc.
We think we would like a WP Site so that we can use the dynamic and static sides of it's capabilities. We also want to have something that acts as a membership side where members can post their Bio and CV's and prospective employers can post help wanted ads.

Target Market(s)

Pediatricians, Pediatric Dentist, Employers seeking these doctors

Industry/Entity Type

Healthcare

Requirements
Must have
• Services:
Resumes/Bio
Help Wanted
Continuing Education Programs
Marketing & Management

```html
<!DOCTYPE html>
<html lang="en">
<head>
<meta charset="utf-8">
<title>Brightwell Practice Partners</title>
<link rel="stylesheet" href="https://fonts.googleapis.com/css2?family=Ubuntu:wght@300;400;500&family=Open+Sans:ital,wght@0,400;0,600;1,400&family=Tinos&display=swap">
<style>
:root{
  --navy:#1d2a48;
  --navy-2:#2b3b60;
  --sky:#5fb8ea;
  --sky-light:#9fd6f6;
  --bar:#4aa6e0;
  --blue-text:#2a9fe0;
  --ink:#333;
  --muted:#666;
  --orange:#f39c12;
  --orange-text:#e8890c;
  --yellow:#ffd21f;
  --line:#d6d6d6;
  --foot:#efefef;
}
*{box-sizing:border-box;margin:0;padding:0}
html,body{width:888px;height:1200px;overflow:hidden;background:#fff}
body{position:relative;font-family:"Open Sans",sans-serif;color:var(--ink)}
.abs{position:absolute}

.header{left:0;top:0;width:888px;height:120px;background:linear-gradient(#18223b,var(--navy-2))}
.brand{left:29px;top:11px;color:#fff;font-family:"Ubuntu",sans-serif;font-weight:500;font-size:20px}
.utility{right:85px;top:8px;color:#c9d1e3;font-size:9.5px}
.utility span{margin:0 4px}
.nav{left:75px;top:75px;display:flex;align-items:center;color:#fff;font-family:"Ubuntu",sans-serif;font-size:12.5px}
.nav a{color:#fff;text-decoration:none;padding:6px 19px}
.nav a.active{background:#131b30;border-radius:14px}
.nav .sep{color:#fff;opacity:.9}

.hero{left:0;top:120px;width:888px;height:260px;background:radial-gradient(circle at 660px 90px,#d8f0ff 0,var(--sky-light) 25%,var(--sky) 70%,#3c9fdd 100%);overflow:hidden}
.hero-card{left:29px;top:30px;width:425px;height:188px;background:rgba(120,190,235,.55);border-radius:8px}
.hero-card h1{position:absolute;left:25px;top:20px;color:#fff;font-family:"Ubuntu",sans-serif;font-weight:300;font-size:36px}
.hero-card p{position:absolute;left:25px;top:75px;width:390px;color:#fff;font-size:10px;line-height:1.6}
.upload{position:absolute;left:24px;top:128px;width:340px;height:30px;background:#fff;border-radius:3px;padding:8px 12px;color:#999;font-size:11.5px}
.upload-btn{position:absolute;left:263px;top:125px;width:101px;height:35px;background:var(--yellow);border-radius:7px;color:#333;font-family:"Ubuntu",sans-serif;font-size:14px;text-align:center;line-height:35px}
.portrait{left:537px;top:25px;width:266px;height:235px;background:linear-gradient(160deg,#6b4a30 0,#d9a98a 35%,#f1d2bc 60%,#f7f7f7 100%);border-radius:120px 120px 0 0}

.features{left:0;top:380px;width:888px;height:53px;background:var(--bar);border-bottom:3px solid #7cc6f0;display:flex}
.feature{height:50px;display:flex;align-items:center;gap:9px;padding-left:38px;color:#fff;font-family:"Ubuntu",sans-serif;font-size:16.5px;border-right:1px solid #79c0ec}
.feature:last-child{border-right:none}

.box{top:457px;height:136px;border:1px solid var(--line);border-radius:3px;box-shadow:0 1px 2px rgba(0,0,0,.06);padding:12px 18px}
.box h2,.panel h2{font-family:"Ubuntu",sans-serif;font-weight:400}
.box h2{color:var(--blue-text);font-size:17px;margin-bottom:6px}
.box p{font-size:9.6px;line-height:1.55;color:var(--muted)}
.more{margin-top:8px;display:flex;align-items:center;gap:6px;color:var(--blue-text);font-family:"Ubuntu",sans-serif;font-size:12.5px}

.panel{top:603px;height:512px;border:1px solid var(--line);border-bottom:none;border-radius:4px 4px 0 0}
.panel>h2{position:absolute;left:24px;top:12px;font-size:17px;color:#333}
.candidate{position:absolute;left:20px;width:520px}
.avatar{position:absolute;left:0;top:0;width:86px;height:72px;border:1px solid #ddd;background:linear-gradient(#e6f1fb,#7fb8e8)}
.cand-text{position:absolute;left:93px;top:0;width:430px}
.cand-text h3{font-family:"Ubuntu",sans-serif;font-weight:400;font-size:12.5px;color:#222;margin-bottom:4px}
.cand-text p{font-size:9.6px;line-height:1.45;color:var(--muted)}
.cand-meta{margin-top:6px;font-size:9.6px;color:var(--orange-text)}
.cand-meta span{margin:0 6px;color:#999}
.details{display:inline-block;margin-top:8px;background:var(--orange);color:#fff;font-size:9.6px;padding:3px 11px;border-radius:3px}

.story{position:absolute;left:12px;width:280px}
.quote{font-style:italic;font-size:9.3px;line-height:1.6;color:#555}
.byline{font-family:"Tinos",serif;font-size:11.5px;color:#222;text-align:right}
.rule{position:absolute;left:15px;width:270px;border-top:1px solid #ddd}
.side-head{position:absolute;left:15px;display:flex;align-items:center;gap:8px;font-family:"Ubuntu",sans-serif;font-size:17.5px;color:#333}
.side-body{position:absolute;left:18px;width:270px;font-style:italic;font-size:9.3px;line-height:1.6;color:#555;text-align:justify}
.side-body p+p{margin-top:4px}
.read{position:absolute;right:18px;font-family:"Tinos",serif;font-size:11.5px;color:#111}

.footer{left:0;top:1115px;width:888px;height:85px;background:var(--foot)}
.foot-links{position:absolute;left:19px;top:16px;font-size:10px;color:#555}
.foot-links span{margin:0 9px;color:#888}
.copy{position:absolute;left:19px;top:42px;font-size:10px;color:#555}
</style>
</head>
<body>

<header class="abs header">
  <div class="abs brand">Brightwell Practice Partners</div>
  <div class="abs utility">Member Login<span>|</span>Faq's<span>|</span>Sign Up<span>|</span>Support</div>
  <nav class="abs nav">
    <a class="active">Main</a><a>About Us</a><span class="sep">|</span><a>Jobs/Hire</a><span class="sep">|</span><a>Continuing Education</a><span class="sep">|</span><a>Managment &amp; Marketing</a><span class="sep">|</span><a>Update</a><span class="sep">|</span><a>Contact</a>
  </nav>
</header>

<section class="abs hero">
  <div class="abs hero-card">
    <h1>Post your Resume Now</h1>
    <p>We at Clearpoint Studio provide you the best simple websites too with total work done as using all the best designing and all done so that you can achieve the goal of yours through our work done on your website.</p>
    <div class="upload">Browse your resume</div>
    <div class="upload-btn">Browse Now</div>
  </div>
  <div class="abs portrait" role="img" aria-label="Photo of a smiling young professional woman"></div>
</section>

<div class="abs features">
  <div class="feature" style="width:213px">
    <svg width="26" height="26" viewBox="0 0 26 26"><path d="M10 2h6v9h5l-8 8-8-8h5z" fill="#fff"/><rect x="2" y="21" width="22" height="3" fill="#fff"/></svg>Post Wanted Ads</div>
  <div class="feature" style="width:170px;padding-left:16px">
    <svg width="26" height="26" viewBox="0 0 26 26" fill="none" stroke="#fff" stroke-width="2"><path d="M4 22l2-7L18 3l5 5-12 12z"/><path d="M15 6l5 5"/></svg>Get Job Offers</div>
  <div class="feature" style="width:222px">
    <svg width="22" height="22" viewBox="0 0 22 22"><path d="M8 1h6v7h7v6h-7v7H8v-7H1V8h7z" fill="#fff"/></svg>Create Resume now</div>
  <div class="feature" style="width:283px;padding-left:24px">
    <svg width="28" height="28" viewBox="0 0 28 28" fill="none" stroke="#fff" stroke-width="4"><path d="M5 13a9 9 0 0 1 16-5"/><path d="M23 15a9 9 0 0 1-16 5"/><path d="M22 2v7h-7M6 26v-7h7" stroke-width="3"/></svg>Check Latest Updates</div>
</div>

<div class="abs box" style="left:17px;width:275px">
  <h2>Job Postings</h2>
  <p>Clearpoint eSolutions is specialized in handling advanced web projects and the ongoing projects that require permanent maintenance and support .We like challenges and do complete</p>
  <div class="more"><svg width="14" height="12" viewBox="0 0 14 12"><path d="M0 4h7V0l7 6-7 6V8H0z" fill="#2a9fe0"/></svg>read more</div>
</div>
<div class="abs box" style="left:303px;width:276px">
  <h2>Check Profile</h2>
  <p>Clearpoint eSolutions is specialized in handling advanced web projects and the ongoing projects that require permanent maintenance and support .We like challenges and do complete</p>
  <div class="more"><svg width="14" height="12" viewBox="0 0 14 12"><path d="M0 4h7V0l7 6-7 6V8H0z" fill="#2a9fe0"/></svg>read more</div>
</div>
<div class="abs box" style="left:590px;width:277px">
  <h2>Sign Up Form</h2>
  <p>Clearpoint eSolutions is specialized in handling advanced web projects and the ongoing projects that require permanent maintenance and support .We like challenges and do complete</p>
  <div class="more"><svg width="14" height="12" viewBox="0 0 14 12"><path d="M0 4h7V0l7 6-7 6V8H0z" fill="#2a9fe0"/></svg>read more</div>
</div>

<section class="abs panel" style="left:17px;width:557px">
  <h2>Latest Resume Updates</h2>
  <div class="candidate" style="top:52px">
    <div class="avatar" role="img" aria-label="Illustrated doctor avatar"></div>
    <div class="cand-text"><h3>Candidate Name here</h3>
      <p>We like challenges and do complete these challenge with expertise we like solving questions that arises in such projects as these helps us to grow also.</p>
      <div class="cand-meta">MBBS, PHD In 2005<span>|</span>5 Year Experience</div>
      <span class="details">full details</span></div>
  </div>
  <div class="candidate" style="top:166px">
    <div class="avatar" role="img" aria-label="Illustrated doctor avatar"></div>
    <div class="cand-text"><h3>Candidate Name here</h3>
      <p>We like challenges and do complete these challenge with expertise we like solving questions that arises in such projects as these helps us to grow also.</p>
      <div class="cand-meta">MBBS, PHD in 2005<span>|</span>5 Year Experience</div>
      <span class="details">full details</span></div>
  </div>
  <div class="candidate" style="top:278px">
    <div class="avatar" role="img" aria-label="Illustrated doctor avatar"></div>
    <div class="cand-text"><h3>Candidate Name here</h3>
      <p>We like challenges and do complete these challenge with expertise we like solving questions that arises in such projects as these helps us to grow also.</p>
      <div class="cand-meta">MBBS, PHD in 2005<span>|</span>5 Year Experience</div>
      <span class="details">full details</span></div>
  </div>
  <div class="candidate" style="top:395px">
    <div class="avatar" role="img" aria-label="Illustrated doctor avatar"></div>
    <div class="cand-text"><h3>Candidate Name here</h3>
      <p>We like challenges and do complete these challenge with expertise we like solving questions that arises in such projects as these helps us to grow also.</p>
      <div class="cand-meta">MBBS, PHD in 2005<span>|</span>5 Year Experience</div>
      <span class="details">full details</span></div>
  </div>
</section>

<aside class="abs panel" style="left:578px;width:299px">
  <h2 style="left:19px">Sucess Stories</h2>
  <div class="abs" style="left:13px;top:49px;width:76px;height:66px;border:1px solid #ccc;background:linear-gradient(#dfe6ea,#8c8f94)" role="img" aria-label="Portrait photo of a satisfied client"></div>
  <div class="story" style="left:94px;top:47px;width:190px">
    <p class="quote"><span style="font-size:14px;color:#aaa">&ldquo;</span> BPP is the perfect solution job seekers are looking for, provided you have content with special language (for objective, goals section etc.) ready beforehand. If you don't, you might want to sit down first and think through exactly what you want from a resume. <span style="font-size:14px;color:#aaa">&rdquo;</span></p>
    <p class="byline" style="margin-top:4px">by Author Name</p>
  </div>
  <div class="rule" style="top:187px"></div>
  <div class="side-head" style="top:202px">
    <svg width="30" height="16" viewBox="0 0 30 16" fill="none" stroke="#3a6ea5" stroke-width="1.3"><path d="M2 13l13-3 13 3M2 13l2-9 11-2 11 2 2 9M15 2v8"/></svg>Continuing Education</div>
  <div class="side-body" style="top:232px">
    <p>Lorem Ipsum is simply dummy text of the printing and typesetting industry. Lorem Ipsum has been the industry's standard dummy text ever since the 1500s.</p>
    <p>when an unknown printer took a galley of type and scrambled it to make a type specimen book</p>
  </div>
  <div class="read" style="top:324px">Read more &gt;&gt;</div>
  <div class="rule" style="top:343px"></div>
  <div class="side-head" style="top:354px">
    <svg width="14" height="24" viewBox="0 0 14 24"><circle cx="7" cy="4" r="3.5" fill="#3d4f6a"/><rect x="3" y="9" width="8" height="14" rx="2" fill="#3d4f6a"/></svg>Managment &amp; Marketing</div>
  <div class="side-body" style="top:385px">
    <p>Lorem Ipsum is simply dummy text of the printing and typesetting industry. Lorem Ipsum has been the industry's standard dummy text ever since the 1500s.</p>
    <p>when an unknown printer took a galley of type and scrambled it to make a type specimen book</p>
  </div>
  <div class="read" style="top:476px;right:15px">Read more &gt;&gt;</div>
</aside>

<footer class="abs footer">
  <div class="foot-links">Main<span>|</span>About Us<span>|</span>Get Job<span>|</span>Post Now<span>|</span>Update<span>|</span>Contact</div>
  <div class="copy">&copy; 2012 Company Name &nbsp;|&nbsp; All right reserved</div>
</footer>

</body>
</html>
```